Company identity deisgn should support 2 languages

I would like to get our company identity design
This includes the following only
Business Cards 2 languages Arabic and English
Email signature
Letterhead
Linkedin profile images
Attached is the logo in Ai format

Requirements
Must have
• For business card
Must have
Name and Adrees in arabic
Name and Address in english
You might use both side of the card
Should not have
• Any pictures other than the logo

```html
<!DOCTYPE html>
<html lang="en">
<head>
<meta charset="utf-8">
<title>Northvale Systems – Business Cards</title>
<link rel="stylesheet" href="https://fonts.googleapis.com/css2?family=Poppins:wght@400;500;600&family=Noto+Naskh+Arabic:wght@400;600&display=swap">
<style>
  :root {
    --brand-blue: #1477c1;
    --ink: #454545;
    --card: #ffffff;
    --backdrop: #e6e6e6;
  }
  * { box-sizing: border-box; margin: 0; padding: 0; }
  html, body { width: 1200px; height: 1200px; overflow: hidden; background: var(--backdrop); }
  .stage {
    position: absolute; left: 0; top: 0;
    width: 1400px; height: 1400px;
    transform: scale(0.857143); transform-origin: 0 0;
    font-family: "Poppins", sans-serif;
  }
  .card {
    position: absolute; left: 306px;
    width: 800px; height: 457px;
    background: var(--card);
    border-radius: 26px;
    overflow: hidden;
  }
  .card--english { top: 193px; }
  .card--arabic { top: 762px; }
  .card__band { position: absolute; left: 0; top: 61px; }
  .card--arabic .card__band { top: 57px; }
  .card__holder {
    position: absolute; left: 44px; top: 64px;
    color: #fff;
  }
  .holder__name { font-size: 26px; font-weight: 500; line-height: 1.1; letter-spacing: 0.3px; }
  .holder__role { font-size: 18px; font-weight: 400; line-height: 1.3; }
  .card--arabic .card__holder { top: 59px; }
  .card--arabic .holder__name, .card--arabic .holder__role {
    font-family: "Noto Naskh Arabic", serif; direction: rtl; text-align: left;
  }
  .card--arabic .holder__name { font-size: 25px; font-weight: 600; line-height: 30px; }
  .card--arabic .holder__role { font-size: 19px; line-height: 22px; }
  .brand {
    position: absolute; right: 42px; top: 60px;
    display: flex; align-items: center; gap: 12px;
    color: var(--brand-blue);
    font-size: 26px; font-weight: 600; letter-spacing: 0.5px;
  }
  .card--arabic .brand { top: 53px; }
  .brand__dot { width: 26px; height: 26px; border-radius: 50%; background: var(--brand-blue); }
  .contacts {
    position: absolute; left: 46px; top: 320px;
    list-style: none; color: var(--ink); font-size: 19px; line-height: 23px;
  }
  .card--arabic .contacts { top: 330px; }
  .contacts li { display: flex; align-items: center; gap: 9px; }
  .contacts svg { width: 16px; height: 16px; fill: var(--brand-blue); flex: none; }
  .address {
    position: absolute; right: 42px; top: 341px;
    color: var(--ink); font-size: 19px; line-height: 23px; text-align: right;
    font-style: normal;
  }
  .address__web { margin-top: 3px; }
  .card--arabic .address { top: 340px; }
  .card--arabic .address__ar { font-family: "Noto Naskh Arabic", serif; direction: rtl; line-height: 26px; }
</style>
</head>
<body>
<div class="stage">

  <section class="card card--english" lang="en">
    <svg class="card__band" width="420" height="60" viewBox="0 0 420 60" aria-hidden="true">
      <polygon points="0,0 390,0 352,60 0,60" fill="var(--brand-blue)"/>
    </svg>
    <div class="card__holder">
      <div class="holder__name">DANIEL HART</div>
      <div class="holder__role">President</div>
    </div>
    <div class="brand"><span class="brand__dot"></span>Northvale Systems</div>
    <ul class="contacts">
      <li><svg viewBox="0 0 16 16"><path d="M3.5 1l2.6 3.3-1.5 1.6c.9 2 2.6 3.7 4.6 4.6l1.6-1.5L14 11.5 12.4 14C7 13.6 2.4 9 2 3.6z"/></svg>555-210-4481</li>
      <li><svg viewBox="0 0 16 16"><path d="M4 1h8v14H4zM5.5 2.5v9.5h5V2.5zM7.2 13h1.6v1H7.2z" fill-rule="evenodd"/></svg>555-318-7720</li>
      <li><svg viewBox="0 0 16 16"><path d="M4 1h8v4H4zM1 6h14v6h-2v3H3v-3H1zM4.5 10v3.5h7V10z" fill-rule="evenodd"/></svg>555-476-1039</li>
      <li><svg viewBox="0 0 16 16"><path d="M1 3.5h14v9H1zM1.5 4l6.5 5 6.5-5" stroke="#fff" stroke-width="1"/></svg>info@northvalesystems.com</li>
    </ul>
    <address class="address">
      <div>4120 Cedar Ridge Way</div>
      <div>Juneau, Alaska 99801</div>
      <div class="address__web">northvalesystems.com</div>
    </address>
  </section>

  <section class="card card--arabic" lang="ar">
    <svg class="card__band" width="460" height="56" viewBox="0 0 460 56" aria-hidden="true">
      <polygon points="0,0 418,0 388,56 0,56" fill="var(--brand-blue)"/>
    </svg>
    <div class="card__holder">
      <div class="holder__name">دانيال هارت</div>
      <div class="holder__role">رئيس</div>
    </div>
    <div class="brand"><span class="brand__dot"></span>Northvale Systems</div>
    <ul class="contacts" lang="en">
      <li><svg viewBox="0 0 16 16"><path d="M3.5 1l2.6 3.3-1.5 1.6c.9 2 2.6 3.7 4.6 4.6l1.6-1.5L14 11.5 12.4 14C7 13.6 2.4 9 2 3.6z"/></svg>555-210-4481</li>
      <li><svg viewBox="0 0 16 16"><path d="M4 1h8v14H4zM5.5 2.5v9.5h5V2.5zM7.2 13h1.6v1H7.2z" fill-rule="evenodd"/></svg>555-318-7720</li>
      <li><svg viewBox="0 0 16 16"><path d="M4 1h8v4H4zM1 6h14v6h-2v3H3v-3H1zM4.5 10v3.5h7V10z" fill-rule="evenodd"/></svg>555-476-1039</li>
      <li><svg viewBox="0 0 16 16"><path d="M1 3.5h14v9H1zM1.5 4l6.5 5 6.5-5" stroke="#fff" stroke-width="1"/></svg>info@northvalesystems.com</li>
    </ul>
    <address class="address">
      <div class="address__ar">4120 طريق سيدار ريدج</div>
      <div class="address__ar">جونو، ألاسكا 99801</div>
      <div class="address__web" lang="en">northvalesystems.com</div>
    </address>
  </section>

</div>
</body>
</html>
```